Logo and Card design for KRV Home Solutions LLC

I need an edgier logo and business card designs. Current logo attached. I like the colors below. I would like the logo to incorporate a home in the design.
Title = Principal-Acquisitions
Email:KRVHOMESOLUTIONS@fernmail.example
555-214-0937
facebook
IG
2 sided business card with the front being contact info a slogan about selling a home fast. The back incorporating What we do. Buy houses, land, or commercial property as is. We find solutions to make the process of selling simple and fair.

Target Market(s)

Motivated house sellers.

Industry/Entity Type

Business

Contact Information for Business Card

Who we are: We are a Faith based Real Estate Investment Company. We pay cash for homes in any condition and can close quick. Whatever the reason you need to sell fast, we can help. We believe in creating win-win solutions to help you in your time of need. We care! We can help!

Logo Text

KRV Home Solutions LLC

Font styles to use
Sans Serif

Colors
33a6d7
0355a3
85abd2
cee9f5
9d9d9d
b2b2b2
ffffff

Requirements
Must have
• Old logo attached. I want something edgier.
• Company name, phone number, description on the back of what we can do. Pay all cash. Buy in as is condition. No fees,Commisions or closing costs.Close quick. No hassles with solutions to meet your unique situation.
• Call today for an offer within 24 hours.

```html
<!DOCTYPE html>
<html lang="en">
<head>
<meta charset="utf-8">
<title>KRV Home Solutions – Business Card</title>
<link href="https://fonts.googleapis.com/css2?family=Lato:wght@400;700&display=swap" rel="stylesheet">
<style>
  :root {
    --backdrop: #b3b6be;
    --navy: #1f3a78;
    --navy-deep: #1c3572;
    --blue-light: #3d62ab;
    --white: #ffffff;
    --ink: #2b2b2b;
    --grey: #8a8c90;
  }
  * { margin: 0; padding: 0; box-sizing: border-box; }
  html, body { width: 1200px; height: 900px; overflow: hidden; }
  body {
    background: var(--backdrop);
    font-family: "Lato", sans-serif;
    position: relative;
  }
  .card {
    position: absolute;
    top: 306px;
    width: 440px;
    height: 272px;
    overflow: hidden;
    box-shadow: 2px 3px 5px rgba(0,0,0,0.45);
  }
  .card--front { left: 149px; background: var(--white); }
  .card--back {
    left: 609px;
    background: linear-gradient(160deg, var(--blue-light) 0%, var(--navy-deep) 45%, #2d4f97 100%);
  }

  /* front */
  .social { position: absolute; top: 24px; right: 26px; display: flex; gap: 6px; }
  .social span { width: 23px; height: 23px; border-radius: 50%; background: var(--navy); display: block; }
  .brand {
    position: absolute; top: 88px; left: 0; width: 100%;
    text-align: center; color: var(--navy);
    font-weight: 700; font-size: 30px; letter-spacing: 0.5px;
  }
  .person { position: absolute; left: 30px; top: 180px; }
  .person__name { color: var(--navy); font-weight: 700; font-size: 16px; text-transform: uppercase; line-height: 20px; }
  .person__title { color: var(--ink); font-size: 13px; line-height: 16px; }
  .contact { position: absolute; left: 208px; top: 180px; color: var(--ink); }
  .contact__row { display: flex; align-items: center; gap: 5px; height: 19px; }
  .contact__row--phone { font-size: 15px; }
  .contact__row--email { font-size: 13px; margin-top: 2px; text-transform: lowercase; }
  .contact svg { width: 10px; height: 10px; fill: var(--navy); flex: none; }
  .front-band {
    position: absolute; left: 0; bottom: 0; width: 100%; height: 46px;
    background: var(--navy); color: var(--white);
    font-weight: 700; font-size: 13px; text-transform: uppercase;
    display: flex; align-items: center; justify-content: center;
  }

  /* back */
  .pitch { position: absolute; left: 37px; top: 21px; color: var(--white); }
  .pitch__heading { font-weight: 700; font-size: 15px; line-height: 18px; margin-bottom: 4px; }
  .pitch__needs { list-style: none; }
  .pitch__needs li { font-weight: 700; font-size: 14px; line-height: 20px; }
  .pitch__needs li::before { content: "●"; font-size: 11px; margin-right: 5px; vertical-align: 1px; }
  .pitch__promises { margin-top: 14px; font-size: 13px; line-height: 20px; }
  .back-band {
    position: absolute; left: 0; bottom: 0; width: 100%; height: 42px;
    background: var(--white); color: var(--navy);
    font-weight: 700; font-size: 15px; text-transform: uppercase;
    display: flex; align-items: center; padding-left: 37px;
  }
</style>
</head>
<body>
  <section class="card card--front">
    <div class="social"><span></span><span></span></div>
    <div class="brand">KRV Home Solutions</div>
    <div class="person">
      <div class="person__name">Marcus Bell</div>
      <div class="person__title">Managing Director</div>
    </div>
    <div class="contact">
      <div class="contact__row contact__row--phone">
        <svg viewBox="0 0 10 10" aria-hidden="true"><path d="M1 3.5C1 2 2.5 1.5 5 1.5S9 2 9 3.5L7.5 4.2 7 3.2H3L2.5 4.2zM2.5 5h5l1 3.5h-7z"/></svg>
        555-214-0937
      </div>
      <div class="contact__row contact__row--email">
        <svg viewBox="0 0 10 10" aria-hidden="true"><path d="M1 2h8v6H1z M1.4 2.4 5 5.4 8.6 2.4" stroke="#fff" stroke-width="0.8"/></svg>
        KRVHOMESOLUTIONS@fernmail.example
      </div>
    </div>
    <div class="front-band">Call today to get an all cash offer within 24 hours</div>
  </section>

  <section class="card card--back">
    <div class="pitch">
      <p class="pitch__heading">KRV Home Solutions can help with your unique situation.</p>
      <ul class="pitch__needs">
        <li>Need Cash?</li>
        <li>Need to sell your house fast?</li>
        <li>Vacant house?</li>
      </ul>
      <p class="pitch__promises">
        We make selling your house easy!<br>
        We buy houses, land or commercial property as is.<br>
        We pay cash and cover all closing costs.<br>
        We make the repairs so you don't have to.<br>
        Close fast and move on with your life!
      </p>
    </div>
    <div class="back-band">Call or text today to hear our cash offer!</div>
  </section>
</body>
</html>
```